Tech business card design

We need an amazing business card design for our new business 'Pexla' a marketing tech startup based in Sydney, Australia. We provide an online marketplace for businesses to search and buy advertising media, connect with service providers and learn more about marketing. We wish to communicate 'cool tech', reliability and professionalism and design based around our logo.

Target Market(s)

Business Owners

Contact Information for Business Card

Name
Position
Email Address
Website
Phone Number

Font styles to use
Other font styles liked:
• Avenir & Avenir Next

Colors

Designer to choose colors to be used in the design.

```html
<!DOCTYPE html>
<html lang="en">
<head>
<meta charset="utf-8">
<title>Pexla Business Card</title>
<link href="https://fonts.googleapis.com/css2?family=Mulish:wght@400;600;800;900&display=swap" rel="stylesheet">
<style>
  :root {
    --stage: #1f2024;
    --navy: #161640;
    --navy-ink: #1b1b48;
    --paper: #ffffff;
    --soft-white: #e9e9f2;
  }
  * { margin: 0; padding: 0; box-sizing: border-box; }
  html, body {
    width: 1200px; height: 800px; overflow: hidden;
    background: var(--stage);
    font-family: "Mulish", Arial, sans-serif;
  }
  .stage {
    width: 1200px; height: 800px;
    display: flex; align-items: center; justify-content: center; gap: 44px;
  }
  .card {
    position: relative;
    width: 530px; height: 303px;
    border-radius: 22px;
    overflow: hidden;
  }
  /* Front */
  .card-front {
    background: var(--navy);
    display: flex; flex-direction: column; align-items: center; justify-content: center;
  }
  .brand-name {
    font-weight: 900;
    color: var(--paper);
    font-size: 104px;
    line-height: 1;
    letter-spacing: -3px;
  }
  .front-web {
    margin-top: 22px;
    color: var(--soft-white);
    font-size: 12px;
    letter-spacing: 6px;
  }
  /* Back */
  .card-back { background: var(--paper); color: var(--navy-ink); }
  .brand-vertical {
    position: absolute;
    left: 34px; top: 50%;
    transform: translateY(-50%) rotate(180deg);
    writing-mode: vertical-rl;
    font-weight: 900;
    font-size: 70px;
    line-height: 1;
    letter-spacing: -2px;
    color: var(--navy-ink);
  }
  .details {
    position: absolute;
    left: 170px; top: 46px; right: 0;
  }
  .person { display: flex; align-items: flex-end; }
  .person-name { font-weight: 800; font-size: 21px; white-space: nowrap; }
  .person-rule {
    flex: 1; height: 1.5px; background: var(--navy-ink);
    margin: 0 0 6px 14px;
  }
  .person-role { font-size: 13px; font-weight: 600; margin-top: 2px; }
  .address { margin-top: 22px; font-size: 14px; line-height: 1.3; }
  .contacts { margin-top: 16px; list-style: none; }
  .contact-row {
    display: flex; align-items: center; gap: 9px;
    font-size: 14px; line-height: 1; margin-bottom: 6px;
  }
  .contact-row strong { font-weight: 800; }
  .contact-icon { width: 17px; height: 17px; flex: none; }
</style>
</head>
<body>
<main class="stage">
  <section class="card card-front" aria-label="Card front">
    <div class="brand-name">Pexla</div>
    <div class="front-web">www.pexlamedia.com</div>
  </section>

  <section class="card card-back" aria-label="Card back">
    <div class="brand-vertical">Pexla</div>
    <div class="details">
      <div class="person">
        <span class="person-name">Mara Lindqvist</span>
        <span class="person-rule"></span>
      </div>
      <div class="person-role">Manager</div>
      <p class="address">PO BOX 480, Harbour Lane<br>14 Kent Street Sydney<br>Australia</p>
      <ul class="contacts">
        <li class="contact-row">
          <svg class="contact-icon" viewBox="0 0 20 20" aria-hidden="true"><circle cx="10" cy="10" r="10" fill="#1b1b48"/><path d="M7 5.5c.6 0 1 1.6 1.2 2.3.1.5-.8.9-.6 1.4.5 1.1 1.3 1.9 2.4 2.4.5.2.9-.7 1.4-.6.7.2 2.3.6 2.3 1.2 0 .9-1 1.8-2 1.8-3.4-.2-6.4-3.2-6.6-6.6 0-1 .9-1.9 1.9-1.9z" fill="#fff"/></svg>
          <span>555.201.7788</span>
        </li>
        <li class="contact-row">
          <svg class="contact-icon" viewBox="0 0 20 20" aria-hidden="true"><circle cx="10" cy="10" r="10" fill="#1b1b48"/><rect x="5" y="6.5" width="10" height="7" rx="1" fill="none" stroke="#fff" stroke-width="1.3"/><path d="M5.3 7l4.7 3.6L14.7 7" fill="none" stroke="#fff" stroke-width="1.3"/></svg>
          <span>hello@pexlamedia.com</span>
        </li>
        <li class="contact-row">
          <svg class="contact-icon" viewBox="0 0 20 20" aria-hidden="true"><circle cx="10" cy="10" r="10" fill="#1b1b48"/><circle cx="10" cy="10" r="5" fill="none" stroke="#fff" stroke-width="1.2"/><path d="M5 10h10M10 5c-2 2.8-2 7.2 0 10M10 5c2 2.8 2 7.2 0 10" fill="none" stroke="#fff" stroke-width="1"/></svg>
          <span>www.<strong>pexlamedia</strong>.com</span>
        </li>
      </ul>
    </div>
  </section>
</main>
</body>
</html>
```